Corvane Capital Business Cards

These are professional business cards that are for my family office.
Put fake emails and phone numbers as of now until I finalize those components. This family office controls my families investments, assets, and future. The cards should be professional.
..
.
.
.
I just uploaded another variation of a logo I would like to see as a business card to I am inbeteen which logo to use

Target Market(s)

business

Industry/Entity Type

business

Contact Information for Business Card

Professional, wealth related, finance related.

Requirements
Must have
• Logo

```html
<!DOCTYPE html>
<html lang="en">
<head>
<meta charset="utf-8">
<title>Corvane Capital Business Cards</title>
<link href="https://fonts.googleapis.com/css2?family=Cinzel:wght@400;600&family=Arimo:wght@400&display=swap" rel="stylesheet">
<style>
  :root {
    --backdrop: #2b2c2f;
    --navy: #1b2030;
    --navy-deep: #171b28;
    --paper: #ffffff;
    --dot-grey: #a9a9a9;
    --ink-light: #f2f3f6;
    --emboss: #3a4258;
  }
  * { box-sizing: border-box; margin: 0; padding: 0; }
  html, body {
    width: 1200px; height: 689px; overflow: hidden;
    background: var(--backdrop);
  }
  .stage {
    position: relative; width: 1200px; height: 689px;
    display: flex; align-items: center; justify-content: center; gap: 60px;
  }
  .card {
    position: relative; width: 510px; height: 292px;
    border-radius: 14px; overflow: hidden;
  }

  /* Back of card */
  .card-back { background: var(--navy-deep); }
  .back-brand {
    position: absolute; left: 0; right: 0; top: 70px;
    display: flex; flex-direction: column; align-items: center; gap: 14px;
  }
  .back-brand .mark-ring {
    width: 92px; height: 92px; border-radius: 50%;
    border: 2px solid var(--emboss);
  }
  .back-brand .brand-name {
    font-family: "Cinzel", serif; font-weight: 400; font-size: 22px;
    letter-spacing: 1px; color: var(--emboss);
  }
  .back-web {
    position: absolute; left: 0; right: 0; bottom: 40px; text-align: center;
    font-family: "Arimo", sans-serif; font-size: 14px; letter-spacing: 3px;
    color: var(--ink-light);
  }

  /* Front of card */
  .card-front { background: var(--paper); }
  .card-front .shapes { position: absolute; inset: 0; }
  .front-brand {
    position: absolute; left: 30px; top: 132px; width: 196px;
    display: flex; flex-direction: column; align-items: center; gap: 12px;
  }
  .front-brand .mark-ring {
    width: 76px; height: 76px; border-radius: 50%;
    border: 2px solid var(--navy);
  }
  .front-brand .brand-name {
    font-family: "Cinzel", serif; font-weight: 400; font-size: 19px;
    letter-spacing: 0.5px; color: var(--navy); white-space: nowrap;
  }
  .contact {
    position: absolute; right: 26px; top: 26px; text-align: right;
    color: var(--ink-light); font-family: "Arimo", sans-serif;
  }
  .contact .person {
    font-family: "Cinzel", serif; font-weight: 600; font-size: 21px;
    letter-spacing: 0.5px; line-height: 1.1;
  }
  .contact .role { font-size: 11px; margin-bottom: 16px; }
  .contact .address { font-size: 12px; line-height: 1.4; margin-bottom: 12px; }
  .contact .line {
    display: flex; justify-content: flex-end; align-items: center; gap: 7px;
    font-size: 12px; line-height: 1.5;
  }
  .contact .line svg { width: 11px; height: 11px; fill: var(--ink-light); }
</style>
</head>
<body>
<main class="stage">

  <section class="card card-back" aria-label="Card back">
    <div class="back-brand">
      <span class="mark-ring"></span>
      <span class="brand-name">Corvane Capital</span>
    </div>
    <p class="back-web">www.corvanecapital.com</p>
  </section>

  <section class="card card-front" aria-label="Card front">
    <svg class="shapes" width="510" height="292" viewBox="0 0 510 292" aria-hidden="true">
      <path d="M 268 -20 A 185 185 0 0 0 328 262" fill="none" stroke="var(--navy)" stroke-width="7"/>
      <circle cx="420" cy="100" r="172" fill="var(--navy)"/>
      <g fill="var(--dot-grey)">
        <ellipse cx="260" cy="24" rx="14" ry="12"/>
        <ellipse cx="252" cy="70" rx="14" ry="12"/>
        <ellipse cx="252" cy="116" rx="14" ry="12"/>
        <ellipse cx="260" cy="162" rx="14" ry="12"/>
        <ellipse cx="276" cy="204" rx="14" ry="12"/>
      </g>
    </svg>

    <div class="front-brand">
      <span class="mark-ring"></span>
      <span class="brand-name">Corvane Capital</span>
    </div>

    <div class="contact">
      <p class="person">Daniel Hart</p>
      <p class="role">President</p>
      <p class="address">1420 Alder Court<br>Northfield, Canada 48210</p>
      <p class="line">555-210-4871
        <svg viewBox="0 0 24 24"><path d="M6.6 10.8a15 15 0 0 0 6.6 6.6l2.2-2.2c.3-.3.7-.4 1-.2 1.1.4 2.3.6 3.6.6.6 0 1 .4 1 1V20c0 .6-.4 1-1 1A17 17 0 0 1 3 4c0-.6.4-1 1-1h3.5c.6 0 1 .4 1 1 0 1.3.2 2.5.6 3.6.1.3 0 .7-.2 1z"/></svg>
      </p>
      <p class="line">555-390-6128
        <svg viewBox="0 0 24 24"><path d="M7 1h10a2 2 0 0 1 2 2v18a2 2 0 0 1-2 2H7a2 2 0 0 1-2-2V3a2 2 0 0 1 2-2zm0 3v14h10V4zm5 15.5a1 1 0 1 0 0 2 1 1 0 0 0 0-2z"/></svg>
      </p>
      <p class="line">info@corvanecapital.com
        <svg viewBox="0 0 24 24"><path d="M2 5h20v14H2zm2 2v.5l8 5 8-5V7zm0 3v7h16v-7l-8 5z"/></svg>
      </p>
      <p class="line">www.corvanecapital.com
        <svg viewBox="0 0 24 24"><path d="M12 2a10 10 0 1 0 0 20 10 10 0 0 0 0-20zm0 2c.9 1.2 1.6 2.8 1.9 5h-3.8c.3-2.2 1-3.8 1.9-5zM4.3 11h3.8c0 1 .1 1.9.3 2.8H5a8 8 0 0 1-.7-2.8zm15.4 0a8 8 0 0 1-.7 2.8h-3.4c.2-.9.3-1.8.3-2.8zm-9.6 0h3.8c0 1-.1 1.9-.3 2.8h-3.2c-.2-.9-.3-1.8-.3-2.8zm.4 4.8h3c-.4 1.7-.9 3-1.5 4-.6-1-1.1-2.3-1.5-4z"/></svg>
      </p>
    </div>
  </section>

</main>
</body>
</html>
```